Low Testosterone Center Postcard Design

I need a jumbo direct mail marketing postcard for my men's low testosterone center. We evaluate and treat men with symptoms related to low testosterone. See my website www.oakridgewellclinic.com for more info on the symptoms of low testosterone and the benefits from bio identical replacement therapy. We have physician oversight for our program. Images and documents are available on my website.

Industry/Entity Type

Marketing

```html
<!DOCTYPE html>
<html lang="en">
<head>
<meta charset="utf-8">
<title>Oak Ridge Well Clinic – Low Testosterone Postcard</title>
<link href="https://fonts.googleapis.com/css2?family=Jost:wght@300;400;500;600;700&display=swap" rel="stylesheet">
<style>
  :root{
    --page-bg:#6b6b6b;
    --brand-blue:#0a6fbd;
    --navy:#131c3a;
    --accent-yellow:#f6b91c;
    --white:#ffffff;
    --sky-top:#cfe3f2;
    --sky-mid:#a9cbe6;
    --sea:#5f93bd;
    --foliage:#5f7a3a;
  }
  *{margin:0;padding:0;box-sizing:border-box}
  html,body{width:1200px;height:809px;overflow:hidden;background:var(--page-bg)}
  body{font-family:"Jost",sans-serif;color:var(--white)}
  .postcard{position:absolute;left:52px;top:52px;width:1096px;height:705px;overflow:hidden;background:var(--white)}
  .postcard__art{position:absolute;inset:0}
  .copy{position:absolute;left:30px;top:0;width:540px}
  .eyebrow{position:absolute;top:32px;font-size:29px;font-weight:600;letter-spacing:.3px;white-space:nowrap}
  .headline{position:absolute;top:62px;font-size:65px;font-weight:700;line-height:73px;letter-spacing:-.3px;white-space:nowrap}
  .headline .accent{color:var(--accent-yellow)}
  .subhead{position:absolute;top:226px;font-size:27px;font-weight:300;line-height:31px;width:475px}
  .body-text{position:absolute;top:343px;font-size:17px;font-weight:400;line-height:21.6px;width:400px}
  .body-text strong{font-weight:600}
  .cta-lead{position:absolute;top:534px;font-size:17px;font-weight:600;color:var(--accent-yellow);white-space:nowrap}
  .cta-main{position:absolute;top:555px;font-size:25px;font-weight:600;color:var(--accent-yellow);letter-spacing:.3px;white-space:nowrap}
  .phone{position:absolute;top:601px;font-size:48px;line-height:48px;font-weight:600;letter-spacing:.5px;white-space:nowrap}
  .website{position:absolute;top:650px;font-size:19px;font-weight:600;color:var(--accent-yellow);white-space:nowrap}
  .brand{position:absolute;right:0;bottom:22px;width:220px;text-align:center}
  .brand__dot{width:92px;height:92px;border-radius:50%;background:var(--accent-yellow);margin:0 auto 14px}
  .brand__name{font-size:19px;font-weight:600;line-height:24px;letter-spacing:.5px;color:var(--white)}
</style>
</head>
<body>
  <div class="postcard">
    <svg class="postcard__art" width="1096" height="705" viewBox="0 0 1096 705">
      <defs>
        <linearGradient id="photoTone" x1="0" y1="0" x2="0" y2="1">
          <stop offset="0" stop-color="var(--sky-top)"/>
          <stop offset=".55" stop-color="var(--sky-mid)"/>
          <stop offset=".85" stop-color="var(--sea)"/>
          <stop offset="1" stop-color="var(--foliage)"/>
        </linearGradient>
      </defs>
      <rect role="img" aria-label="Photo of a smiling young couple, woman riding piggyback on man, with sky and sea behind" x="340" y="0" width="760" height="705" fill="url(#photoTone)"/>
      <polygon points="0,0 652,0 352,705 0,705" fill="#ffffff"/>
      <polygon points="0,0 646,0 346,705 0,705" fill="var(--brand-blue)"/>
      <polygon points="1096,122 1096,705 840,705" fill="#ffffff"/>
      <polygon points="1096,132 1096,705 848,705" fill="var(--navy)"/>
    </svg>

    <div class="copy">
      <p class="eyebrow">TRUSTED CENTER FOR</p>
      <h1 class="headline">TREATING <span class="accent">LOW</span><br>TESTOSTERONE</h1>
      <p class="subhead">HELPING MEN CHANGE THEIR LIVES AND REGAIN THEIR CONFIDENCE FOR OVER 20 YEARS</p>
      <p class="body-text">The <strong>Oak Ridge Well Clinic</strong> is to diagnose and treat men with symptoms of low testosterone, otherwise known as hypogonadism in a quick, efficient, inexpensive and safe manner. We believe that testosterone replacement therapy can improve overall quality of life and can be done very safely in the comfort of an office whose specialty is men’s health.</p>
      <p class="cta-lead">Make an Appointment with Us and</p>
      <p class="cta-main">CHANGE YOUR LIFE TODAY!</p>
      <p class="phone">732-555-0186</p>
      <p class="website">www.oakridgewellclinic.com</p>
    </div>

    <div class="brand">
      <div class="brand__dot"></div>
      <p class="brand__name">OAK RIDGE<br>WELL CLINIC</p>
    </div>
  </div>
</body>
</html>
```